Small Business Broker Business Card Design

A business card design for a small business brokerage, which is a financial service, not unlike real estate brokerage, but for small businesses such as laundromats, pizza shops, restaurants, cleaners etc. The designs should all be simple, more conservative in nature, using the colors and font of the logo. Again, think real estate Brokerage as a business context
Contact Information for Business Card
Name: Glen R. Harlow. Title: Small Business Advisor. Email: g.harlow@bayfieldcapitalworks.example. Mobile: (555) 274-3918. Office: (555) 806-2147. www.bayfieldcapitalworks.example

```html
<!DOCTYPE html>
<html lang="en">
<head>
<meta charset="utf-8">
<title>Bayfield Capital Works – Business Card</title>
<link rel="stylesheet" href="https://fonts.googleapis.com/css2?family=Montserrat:wght@600;700&family=Open+Sans:wght@300;400&display=swap">
<style>
  :root {
    --stage: #121314;
    --navy: #17305e;
    --navy-light: #1c3a6e;
    --green: #8dc63f;
    --white: #ffffff;
  }
  * { margin: 0; padding: 0; box-sizing: border-box; }
  html, body { width: 1200px; height: 963px; overflow: hidden; }
  body {
    background: var(--stage);
    display: flex;
    align-items: center;
    justify-content: center;
    gap: 44px;
    font-family: "Open Sans", Arial, sans-serif;
  }
  .card {
    position: relative;
    width: 520px;
    height: 297px;
    border-radius: 18px;
    overflow: hidden;
    background: radial-gradient(circle at 55% 45%, var(--navy-light), var(--navy) 70%);
    color: var(--white);
  }
  .brand { font-family: "Montserrat", Arial, sans-serif; }
  .brand-name {
    font-weight: 700;
    font-size: 17px;
    letter-spacing: 0.04em;
    text-transform: uppercase;
    color: var(--white);
    line-height: 1.1;
    white-space: nowrap;
  }
  .brand-tagline {
    font-weight: 600;
    font-size: 8.6px;
    letter-spacing: 0.12em;
    text-transform: uppercase;
    color: var(--green);
    margin-top: 3px;
    white-space: nowrap;
  }
  /* front */
  .card-front .brand { position: absolute; top: 30px; left: 150px; }
  .person { position: absolute; top: 92px; left: 38px; }
  .person-name {
    font-family: "Montserrat", Arial, sans-serif;
    font-weight: 700;
    font-size: 21px;
    letter-spacing: 0.03em;
    text-transform: uppercase;
  }
  .person-title { font-weight: 300; font-size: 14px; color: var(--green); margin-top: 2px; }
  .contact-list { position: absolute; top: 168px; left: 38px; list-style: none; }
  .contact-list li {
    display: flex; align-items: center; gap: 8px;
    font-size: 12.5px; line-height: 21px; font-weight: 400;
    white-space: nowrap;
  }
  .contact-list svg { width: 12px; height: 12px; flex: none; fill: none; stroke: var(--green); stroke-width: 1.6; }
  .corner-panel {
    position: absolute; right: 0; bottom: 0;
    width: 150px; height: 110px;
    background: var(--white);
    border-top-left-radius: 4px;
  }
  .corner-panel .mark {
    position: absolute; right: 26px; bottom: 26px;
    width: 56px; height: 56px;
    background: var(--green);
  }
  /* back */
  .card-back { display: flex; align-items: center; justify-content: center; }
  .card-back .brand { display: flex; align-items: center; gap: 16px; }
  .card-back .brand-name { font-size: 19px; }
  .card-back .mark { width: 46px; height: 46px; background: var(--green); flex: none; }
</style>
</head>
<body>
  <section class="card card-front" aria-label="Business card front">
    <div class="brand">
      <div class="brand-name">Bayfield Capital Works, Inc</div>
      <div class="brand-tagline">Trusted guidance to buy or sell your business</div>
    </div>
    <div class="person">
      <div class="person-name">Glen R. Harlow</div>
      <div class="person-title">Small Business Advisor</div>
    </div>
    <ul class="contact-list">
      <li><svg viewBox="0 0 12 12"><path d="M3 1.5l1.8 2.2-1 1.2a6 6 0 0 0 3.3 3.3l1.2-1 2.2 1.8-1 1.5C5.5 10.5 1.5 6.5 1.5 2.5z"/></svg>(555) 806-2147</li>
      <li><svg viewBox="0 0 12 12"><rect x="3" y="1" width="6" height="10" rx="1"/><path d="M5.5 9.3h1"/></svg>(555) 274-3918</li>
      <li><svg viewBox="0 0 12 12"><rect x="1" y="2.5" width="10" height="7" rx="0.8"/><path d="M1.3 3l4.7 3.6L10.7 3"/></svg>g.harlow@bayfieldcapitalworks.example</li>
      <li><svg viewBox="0 0 12 12"><circle cx="6" cy="6" r="4.8"/><ellipse cx="6" cy="6" rx="2" ry="4.8"/><path d="M1.2 6h9.6"/></svg>www.bayfieldcapitalworks.example</li>
    </ul>
    <div class="corner-panel"><div class="mark"></div></div>
  </section>

  <section class="card card-back" aria-label="Business card back">
    <div class="brand">
      <div class="mark"></div>
      <div>
        <div class="brand-name">Bayfield Capital Works, Inc</div>
        <div class="brand-tagline">Trusted guidance to buy or sell your business</div>
      </div>
    </div>
  </section>
</body>
</html>
```